Fabric Store Business card

Need a business card portraying store logo and up and coming business of quilt fabrics, apparel fabrics, notions and buttons. Our business name is Gilded Thimble and Beyond. Am attaching logo. The design should communicate a growing business and warm atmosphere. Would like address and store hours and contact info displayed on card. Mon - Fri 9:30 to 5:00, Saturday 9:30 to 1:00. Address 784 W Orchard Ave, Newton, KS 67230 email: gildedthimblebeyond@mailvexa.com. Phone and fax 316-527-3486. After hours contact # 620-431-9052 Also like vintage sewing machines and dress forms if it works to incorporate fine, if not thats ok too.
Store

```html
<!DOCTYPE html>
<html lang="en">
<head>
<meta charset="utf-8">
<title>Gilded Thimble and Beyond – Business Card</title>
<link rel="stylesheet" href="https://fonts.googleapis.com/css2?family=Didact+Gothic&family=Great+Vibes&display=swap">
<style>
  :root {
    --stage: #2b2b2b;
    --red: #c41e2e;
    --red-deep: #a5121f;
    --maroon: #4a0b10;
    --ink: #1e1e1e;
    --paper: #ffffff;
    --paper-shade: #ececec;
    --stitch-dark: #2a2a2a;
    --blush: #e8c3c6;
    --muted-red: #b9898c;
    --cream: #f6dcdc;
  }
  * { box-sizing: border-box; margin: 0; padding: 0; }
  html, body { width: 1200px; height: 900px; overflow: hidden; background: var(--stage); }
  body { position: relative; font-family: "Didact Gothic", "Century Gothic", sans-serif; }

  .card {
    position: absolute;
    width: 540px;
    height: 310px;
    border-radius: 22px;
    overflow: hidden;
  }
  .stitch-frame {
    position: absolute;
    inset: 14px;
    border-radius: 16px;
    border: 2px dashed var(--stitch-dark);
  }

  /* Back card */
  .card-back {
    left: 80px; top: 90px;
    background: linear-gradient(160deg, var(--red) 0%, var(--red-deep) 100%);
  }
  .hours-title {
    position: absolute; left: 60px; top: 40px;
    font-family: "Great Vibes", cursive;
    font-size: 42px; color: var(--maroon);
  }
  .hours-grid {
    position: absolute; left: 68px; top: 100px;
    display: grid; grid-template-columns: 112px auto; row-gap: 2px;
    font-size: 17px; color: var(--maroon);
  }
  .hours-grid .time { color: var(--cream); }
  .product-line {
    position: absolute; left: 60px; top: 178px;
    font-size: 17px; color: var(--maroon);
  }
  .after-hours {
    position: absolute; left: 60px; top: 236px;
    font-size: 17px; color: var(--cream);
  }

  /* Front card */
  .card-front {
    left: 580px; top: 500px;
    background: linear-gradient(170deg, var(--paper) 55%, var(--paper-shade) 100%);
  }
  .corner-accent {
    position: absolute; right: -30px; top: -40px;
    width: 120px; height: 120px; border-radius: 50%;
    background: var(--blush); opacity: 0.7;
  }
  .brand {
    position: absolute; left: 110px; top: 62px;
    display: flex; align-items: center; gap: 14px;
  }
  .brand-dot {
    width: 52px; height: 52px; border-radius: 50%;
    background: var(--red);
  }
  .brand-name {
    font-size: 26px; color: var(--red-deep);
  }
  .person {
    position: absolute; right: 40px; top: 140px; text-align: right;
  }
  .person-name { font-size: 24px; color: var(--red-deep); letter-spacing: 0.5px; line-height: 1; }
  .person-role { font-size: 13px; color: var(--ink); margin-top: 2px; }
  .shears-art {
    position: absolute; right: 50px; top: 196px;
    width: 150px; height: 34px; border-radius: 17px;
    background: linear-gradient(90deg, var(--muted-red), #d8b9bb);
    opacity: 0.8;
  }
  .icon-tab {
    position: absolute; left: 14px; top: 160px;
    width: 42px; height: 136px;
    background: var(--red);
    border-radius: 0 10px 10px 0;
    display: flex; flex-direction: column; justify-content: space-around; align-items: center;
    padding: 6px 0;
  }
  .icon-tab svg { width: 20px; height: 20px; fill: var(--paper); }
  .contact-list {
    position: absolute; left: 72px; top: 164px;
    list-style: none; font-size: 15px; color: var(--ink);
    display: flex; flex-direction: column; gap: 12px;
  }
</style>
</head>
<body>

<section class="card card-back">
  <div class="stitch-frame"></div>
  <h2 class="hours-title">Store hours</h2>
  <div class="hours-grid">
    <span>Mon - Fri</span><span>Saturday</span>
    <span class="time">9:30 to 5:00</span><span class="time">9:30 to 1:00</span>
  </div>
  <p class="product-line">Quilt Fabrics, Apparel Fabrics, Notions &amp; Buttons</p>
  <p class="after-hours">After hours contact # 620-431-9052</p>
</section>

<section class="card card-front">
  <div class="corner-accent" role="img" aria-label="Large faint sewing button decoration"></div>
  <div class="stitch-frame"></div>

  <div class="brand">
    <span class="brand-dot"></span>
    <span class="brand-name">Gilded Thimble and Beyond</span>
  </div>

  <div class="person">
    <p class="person-name">YOUR NAME</p>
    <p class="person-role">Designation</p>
  </div>
  <div class="shears-art" role="img" aria-label="Faint illustration of sewing scissors"></div>

  <div class="icon-tab">
    <svg viewBox="0 0 24 24" aria-label="Phone"><path d="M3 8c0-2 2-4 9-4s9 2 9 4v2h-5V8H8v2H3z M6 12h12l2 8H4z"/></svg>
    <svg viewBox="0 0 24 24" aria-label="Fax"><path d="M7 3h10v6H7z M3 10h18v8h-4v-3H7v3H3z M8 16h8v5H8z"/></svg>
    <svg viewBox="0 0 24 24" aria-label="Email"><path d="M2 5h20v14H2z M3 6l9 7 9-7v1l-9 7-9-7z" fill-rule="evenodd"/></svg>
    <svg viewBox="0 0 24 24" aria-label="Location"><path d="M12 2a7 7 0 0 1 7 7c0 5-7 13-7 13S5 14 5 9a7 7 0 0 1 7-7zm0 4a3 3 0 1 0 0 6 3 3 0 0 0 0-6z" fill-rule="evenodd"/></svg>
  </div>

  <ul class="contact-list">
    <li>316-527-3486</li>
    <li>316-527-3486</li>
    <li>gildedthimblebeyond@mailvexa.com</li>
    <li>784 W Orchard Ave, Newton, KS 67230</li>
  </ul>
</section>

</body>
</html>
```